KTR Design Business Card

I need to develop a business card for my real estate design and investment company. Something clean, classic and professional with a modern vibe.

Industry/Entity Type

Real Estate

Font styles to use
Serif
Sans Serif

```html
<!DOCTYPE html>
<html lang="en">
<head>
<meta charset="utf-8">
<title>KTR Design Business Card</title>
<link rel="stylesheet" href="https://fonts.googleapis.com/css2?family=Arimo:wght@400;500&family=Jost:wght@300;400&display=swap">
<style>
  :root {
    --backdrop: #e8e8e8;
    --card-dark: #262626;
    --card-dark-edge: #1c1c1c;
    --card-light: #f4f4f4;
    --ink-dark: #1e1e1e;
    --ink-light: #ffffff;
    --ink-soft: #e2e2e2;
  }
  * { margin: 0; padding: 0; box-sizing: border-box; }
  html, body {
    width: 1200px;
    height: 720px;
    overflow: hidden;
    background: var(--backdrop);
  }
  .canvas {
    position: relative;
    width: 1200px;
    height: 720px;
  }
  .card {
    position: absolute;
    top: 242px;
    width: 420px;
    height: 240px;
    overflow: hidden;
  }
  .card--front { left: 147px; background: var(--card-dark); }
  .card--back {
    left: 633px;
    background: linear-gradient(135deg, #2b2b2b 0%, var(--card-dark-edge) 100%);
  }
  .front-brand-panel {
    position: absolute;
    left: 0; top: 0;
    width: 210px;
    height: 240px;
    background: var(--card-light);
  }
  .front-notch {
    position: absolute;
    left: 210px;
    top: 56px;
    width: 10px;
    height: 20px;
  }
  .brand-name {
    position: absolute;
    font-family: "Jost", sans-serif;
    font-weight: 300;
    letter-spacing: 0.04em;
    white-space: nowrap;
    display: flex;
    align-items: center;
    gap: 10px;
  }
  .brand-mark {
    display: inline-block;
    border: 1.5px solid currentColor;
  }
  .card--front .brand-name {
    color: var(--ink-dark);
    font-size: 24px;
    left: 105px;
    top: 126px;
    transform: translate(-50%, -50%);
  }
  .card--front .brand-mark { width: 14px; height: 14px; }
  .card--back .brand-name {
    color: var(--ink-light);
    font-size: 32px;
    left: 210px;
    top: 118px;
    transform: translate(-50%, -50%);
  }
  .card--back .brand-mark { width: 18px; height: 18px; }
  .contact-block {
    position: absolute;
    left: 247px;
    top: 52px;
    font-family: "Arimo", sans-serif;
    color: var(--ink-soft);
  }
  .contact-name {
    font-size: 13px;
    font-weight: 500;
    color: var(--ink-light);
    line-height: 1.1;
  }
  .contact-role {
    font-size: 9.5px;
    line-height: 1.3;
  }
  .contact-address {
    margin-top: 22px;
    font-size: 9.5px;
    line-height: 1.3;
    width: 140px;
  }
  .contact-list {
    list-style: none;
    margin-top: 16px;
    font-size: 9.5px;
  }
  .contact-list li {
    display: flex;
    align-items: center;
    gap: 8px;
    height: 12px;
  }
  .contact-list svg {
    width: 10px;
    height: 9px;
    flex: none;
  }
</style>
</head>
<body>
<main class="canvas">

  <section class="card card--front" aria-label="Business card front">
    <div class="front-brand-panel"></div>
    <svg class="front-notch" viewBox="0 0 10 20" aria-hidden="true">
      <polygon points="0,0 10,10 0,20" fill="var(--card-light)"/>
    </svg>
    <div class="brand-name"><span class="brand-mark"></span>KTR Design</div>

    <div class="contact-block">
      <p class="contact-name">Marek Ellison</p>
      <p class="contact-role">Founder &amp; CEO</p>
      <p class="contact-address">Here your compnay or home address</p>
      <ul class="contact-list">
        <li>
          <svg viewBox="0 0 10 9" aria-hidden="true"><path d="M0 3 Q5 -1 10 3 L8 4 L7 2.5 L3 2.5 L2 4 Z M2 5 L8 5 L9 9 L1 9 Z" fill="currentColor"/></svg>
          +981 204 376
        </li>
        <li>
          <svg viewBox="0 0 10 9" aria-hidden="true"><rect x="2.5" y="0.5" width="5" height="8" rx="0.8" fill="none" stroke="currentColor"/></svg>
          +983 617 290
        </li>
        <li>
          <svg viewBox="0 0 10 9" aria-hidden="true"><rect x="0.5" y="1" width="9" height="7" fill="none" stroke="currentColor"/><path d="M0.5 1 L5 5 L9.5 1" fill="none" stroke="currentColor"/></svg>
          info@ktrdesign.com
        </li>
        <li>
          <svg viewBox="0 0 10 9" aria-hidden="true"><rect x="0.5" y="0.5" width="9" height="6" fill="none" stroke="currentColor"/><path d="M3 8.5 L7 8.5 M5 6.5 L5 8.5" stroke="currentColor"/></svg>
          www.ktrdesign.com
        </li>
      </ul>
    </div>
  </section>

  <section class="card card--back" aria-label="Business card back">
    <div class="brand-name"><span class="brand-mark"></span>KTR Design</div>
  </section>

</main>
</body>
</html>
```